Book Cover for Lanterns Along the Quiet Threshold

I need a book cover for a 6 x 9 paperback titled Lanterns Along the Quiet Threshold Gathered from Research and Voices Dwelling in the Realm beyond Our Present Days. It has to do with consciousness, the mind, incarnation onto Earth, leaving Earth, and the life in the life after this life. I have an idea I'm providing with this description, but I am open to anything that would be striking and stimulating, whether with a book or not. I am the author, T. Morgan Wexley. I've added another background idea to see if anyone can do something with it and I've increased the budget.

```html
<!DOCTYPE html>
<html lang="en">
<head>
<meta charset="utf-8">
<title>Lanterns Along the Quiet Threshold — Book Cover</title>
<link href="https://fonts.googleapis.com/css2?family=Cinzel:wght@400;700&family=Tinos&display=swap" rel="stylesheet">
<style>
  :root {
    --page-bg: #ffffff;
    --cover-black: #060504;
    --cover-charcoal: #2e2a27;
    --glow-core: #fff3cf;
    --glow-warm: #c98a2c;
    --glow-deep: #5a3a14;
    --gold: #d9b677;
    --gold-deep: #b58f4f;
    --white: #ffffff;
  }
  * { margin: 0; padding: 0; box-sizing: border-box; }
  html, body {
    width: 1200px;
    height: 1200px;
    overflow: hidden;
    background: var(--page-bg);
  }
  .cover {
    position: absolute;
    left: 220px;
    top: 30px;
    width: 760px;
    height: 1140px;
    background:
      radial-gradient(ellipse 48% 34% at 50% 62%, rgba(201,138,44,0.85) 0%, rgba(90,58,20,0.55) 45%, rgba(6,5,4,0) 100%),
      linear-gradient(160deg, var(--cover-charcoal) 0%, #141110 35%, var(--cover-black) 70%);
    overflow: hidden;
  }
  .title-main {
    position: absolute;
    top: 92px;
    left: 0;
    width: 100%;
    text-align: center;
    font-family: "Cinzel", serif;
    font-weight: 400;
    font-size: 104px;
    line-height: 1;
    letter-spacing: 1px;
    color: var(--gold);
    text-shadow: 0 2px 0 var(--gold-deep);
  }
  .title-sub {
    position: absolute;
    top: 232px;
    left: 0;
    width: 100%;
    text-align: center;
    font-family: "Cinzel", serif;
    font-weight: 700;
    font-size: 31px;
    line-height: 1;
    color: var(--gold);
  }
  .tagline {
    position: absolute;
    top: 290px;
    left: 40px;
    right: 40px;
    text-align: center;
    font-family: "Tinos", serif;
    font-size: 31px;
    line-height: 1.3;
    color: var(--white);
  }
  .book-art {
    position: absolute;
    left: 70px;
    top: 560px;
    width: 620px;
    height: 290px;
    border-radius: 50% 50% 8% 8% / 40% 40% 10% 10%;
    background:
      radial-gradient(ellipse 30% 45% at 50% 30%, var(--glow-core) 0%, rgba(255,243,207,0) 100%),
      linear-gradient(180deg, #e8c98f 0%, #b8874a 55%, #4a2f15 100%);
    opacity: 0.9;
  }
  .author {
    position: absolute;
    top: 1000px;
    left: 0;
    width: 100%;
    text-align: center;
    font-family: "Cinzel", serif;
    font-weight: 700;
    font-size: 52px;
    line-height: 1;
    color: var(--white);
  }
</style>
</head>
<body>
  <main class="cover">
    <h1 class="title-main">LANTERNS</h1>
    <p class="title-sub">Along the Quiet Threshold</p>
    <p class="tagline">Gathered from Research and Voices<br>Dwelling in the Realm beyond Our Present Days</p>
    <div class="book-art" role="img" aria-label="An old open book with fanning pages, glowing with warm golden light from its center"></div>
    <p class="author">T. Morgan Wexley</p>
  </main>
</body>
</html>
```